Wordpress Design Project

I have a main site www.tinymolarclinic.example for 9 dental offices. I want a designed wordpress mini-site template that I can use to create mini sites for each location and related projects that keeps the look and feel of the home site.
Updates

I'm getting different designs from my original web site. Maybe I'm confusing the designers but to clarify:

what I want is to keep the same graphics as we already have on this site www.tinymolarclinic.example and just convert it to a Wordpress site template to be used as individual MINI sites. 

No new designs needed, same design just different platform.

Target Market(s)

see site www.tinymolarclinic.example

Industry/Entity Type

Dental

Requirements
Must have
• Can we make the Logo larger?
Should not have
• I think you're basing your designs on tinymolarclinicglendale.example but I specifically said it should be based on the home site which is www.tinymolarclinic.example
Please view the difference. I need for it to have the same APPEARANCE. Please!
http://www.tinymolarclinic.example/

```html
<!DOCTYPE html>
<html lang="en">
<head>
<meta charset="utf-8">
<title>Tiny Molar Clinic</title>
<link rel="stylesheet" href="https://fonts.googleapis.com/css2?family=Fira+Sans+Extra+Condensed:ital,wght@0,500;1,600&family=Lobster&family=PT+Sans:ital,wght@0,400;0,700;1,700&display=swap">
<style>
:root{
  --page:#f1f1f1;
  --band:#e4e4e4;
  --ink:#555;
  --text:#333;
  --magenta:#c0185a;
  --red:#e0262b;
  --green:#3aa935;
  --blue:#2d86d6;
  --blue-dark:#1a5fa8;
  --cyan:#12b7dc;
  --white:#fff;
  --frame:#d4d4d4;
}
*{box-sizing:border-box;margin:0;padding:0}
html,body{width:1043px;height:1200px;overflow:hidden}
body{position:relative;background:radial-gradient(ellipse at 50% 30%,#fafafa 0%,var(--page) 60%,#e9e9e9 100%);font-family:"PT Sans",Arial,sans-serif;color:var(--text)}
.abs{position:absolute}
.brand{left:150px;top:22px;display:flex;align-items:center;gap:10px}
.brand-dot{width:46px;height:46px;border-radius:50%;background:var(--green)}
.brand-name{font-family:"PT Sans",sans-serif;font-weight:700;font-size:26px;color:var(--green);line-height:1.05;width:110px}
.search{left:570px;top:26px;width:176px;height:38px;background:var(--white);border-radius:8px;box-shadow:0 1px 4px rgba(0,0,0,.2);font:11px Arial,sans-serif;color:#666;padding:12px 14px}
.search svg{position:absolute;right:10px;top:13px}
.mascot{left:759px;top:0;width:122px;height:98px;border-radius:40px;background:radial-gradient(circle,#e8e8e8,#d8d8d8 70%,transparent 72%)}
.phone{left:440px;top:69px;font-family:"Fira Sans Extra Condensed",sans-serif;font-style:italic;font-weight:600;font-size:21px;color:var(--red)}
.phone em{font-style:italic;color:var(--green)}
.nav{left:204px;top:104px;display:flex;gap:4px}
.nav a{display:block;height:24px;padding:0 11px 0 20px;border-radius:8px 8px 10px 10px;background:linear-gradient(#6bb3f0,var(--blue) 50%,var(--blue-dark));color:var(--white);font-size:12.5px;line-height:24px;text-decoration:none;position:relative;box-shadow:0 1px 2px rgba(0,0,0,.3)}
.nav a::before{content:"";position:absolute;left:8px;top:10px;width:4px;height:4px;border-radius:50%;background:#bfe0ff}
.mission{left:209px;top:146px;width:310px}
.mission h1{font-weight:700;font-style:italic;font-size:35px;line-height:41px;color:var(--ink);letter-spacing:-.5px}
.mission p{margin:10px 0 0 9px;font-size:17.5px;line-height:20px;color:#555}
.arrow{width:42px;height:42px;border-radius:50%;background:#666;top:244px}
.slide{width:167px;height:119px;background:var(--white);border:1px solid var(--frame);border-radius:5px;padding:5px;box-shadow:0 1px 3px rgba(0,0,0,.1)}
.slide div{width:100%;height:100%}
.dots{left:322px;top:392px;display:flex;gap:3px}
.dots span{width:12px;height:12px;border-radius:50%;background:linear-gradient(#eee,#bbb);border:1px solid #aaa}
.dots .on{background:#444}
.rule{left:195px;top:422px;width:680px;height:1px;background:#d0d0d0}
.welcome{left:158px;top:436px;font-family:"Lobster",cursive;font-size:25px;color:var(--magenta)}
.welcome-copy{left:169px;top:469px;width:466px;font:10.5px/12.5px Arial,sans-serif;color:var(--text)}
.welcome-copy b{display:block;margin-bottom:11px}
.kids{left:640px;top:440px;width:233px;height:164px}
.section-title{top:622px;font-family:"Fira Sans Extra Condensed",sans-serif;font-style:italic;font-weight:600;font-size:25px;color:var(--magenta)}
.section-title.plain{font-style:normal;font-weight:500;font-size:28px;top:618px}
.card{top:650px;width:216px;height:151px;background:var(--white);border:1px solid var(--frame);border-radius:6px;padding:5px;box-shadow:0 1px 3px rgba(0,0,0,.1)}
.card .photo{width:100%;height:100%}
.card .more{position:absolute;right:0;bottom:0;width:112px;height:27px;border-radius:4px 0 6px 0;background:linear-gradient(var(--blue),var(--cyan));color:var(--white);font-family:"Fira Sans Extra Condensed",sans-serif;font-weight:500;font-size:16px;line-height:27px;padding-left:11px}
.band{left:0;top:829px;width:1043px;height:309px;background:var(--band)}
.tagline{left:146px;top:826px;font-family:"Fira Sans Extra Condensed",sans-serif;font-weight:500;font-size:42px;color:#555}
.tagline b{font-style:italic;font-weight:600}
.sub{top:870px;font-family:"Fira Sans Extra Condensed",sans-serif;font-style:italic;font-weight:600;font-size:25px;color:#555}
.services{left:156px;top:898px;list-style:none;font-size:10.5px;line-height:16.8px;color:#555}
.services li::before{content:"• "}
.map{left:352px;top:907px;width:243px;height:188px;border-radius:10px;border:3px solid #444;background:linear-gradient(135deg,#d9e7c4,#ece9d8 45%,#f3d99b 70%,#e9e4d6);box-shadow:0 3px 6px rgba(0,0,0,.35)}
.envelope{left:776px;top:842px}
.field{left:614px;width:216px;height:23px;background:var(--white);border:1px solid #ddd;font:10.5px Arial,sans-serif;color:#aaa;padding:5px 8px}
.footer{left:0;top:1138px;width:1043px;height:62px;background:#f7f7f7;text-align:center;font:10.5px Arial,sans-serif;color:#333;padding-top:11px;line-height:14px}
.footer a{color:#333;text-decoration:none}
</style>
</head>
<body>

<div class="abs brand"><span class="brand-dot"></span><span class="brand-name">Tiny Molar Clinic</span></div>

<div class="abs search">search this site...
<svg width="12" height="12" viewBox="0 0 12 12"><circle cx="5" cy="5" r="3.5" fill="none" stroke="#888" stroke-width="1.3"/><line x1="7.5" y1="7.5" x2="11" y2="11" stroke="#888" stroke-width="1.5"/></svg></div>
<div class="abs mascot" role="img" aria-label="Sketched cartoon mascot decoration"></div>

<div class="abs phone">Call Us Toll-Free: 1-888-<em>TINY-MOL</em> (555-0142)...</div>

<nav class="abs nav">
  <a href="#">Home</a><a href="#">About</a><a href="#">Services</a><a href="#">Gallery</a><a href="#">Appointment</a><a href="#">Promise</a><a href="#">Patient Log In</a><a href="#">FAQ's</a><a href="#">Contact</a>
</nav>

<section class="abs mission">
  <h1>Our mission is to bring smiles for kids.</h1>
  <p>That we treat Smiles that are healthy, individually beautiful yet a universal language that everyone understands.</p>
</section>

<svg class="abs arrow" style="left:169px" viewBox="0 0 42 42"><circle cx="21" cy="21" r="21" fill="#666"/><path d="M25 12 L14 21 L25 30Z" fill="#fff"/></svg>
<svg class="abs arrow" style="left:846px" viewBox="0 0 42 42"><circle cx="21" cy="21" r="21" fill="#666"/><path d="M17 12 L28 21 L17 30Z" fill="#fff"/></svg>

<div class="abs slide" style="left:519px;top:148px"><div role="img" aria-label="Dentist examining a young girl in the dental chair" style="background:linear-gradient(135deg,#d7dde4,#8ab0d0)"></div></div>
<div class="abs slide" style="left:709px;top:148px"><div role="img" aria-label="Smiling blonde girl brushing her teeth" style="background:linear-gradient(135deg,#e8c9a8,#9cc4e0)"></div></div>
<div class="abs slide" style="left:519px;top:283px"><div role="img" aria-label="Laughing girl in a pink knit hat" style="background:linear-gradient(135deg,#e070a8,#8db4d6)"></div></div>
<div class="abs slide" style="left:709px;top:283px"><div role="img" aria-label="Smiling child holding a toothbrush" style="background:linear-gradient(135deg,#7a4a30,#f2efe9)"></div></div>

<div class="abs dots"><span></span><span></span><span class="on"></span><span></span><span></span><span></span></div>
<div class="abs rule"></div>

<h2 class="abs welcome">Welcome to Tiny Molar Clinic.</h2>
<div class="abs welcome-copy">
  <b>Marcus T. Ellory, DDS, had a vision of a place where low and middle-income children can obtain quality, affordable dental treatment without the fear of seeing a dentist and that vision has become a reality at Tiny Molar Clinic.</b>
  Dr. Ellory attended Dental School at Halloway Dental School in Riverton, Ohio on a Public Health scholarship. After his graduation in 1983 Dr. Ellory worked in a Public Health clinic for (4) years, where he became aware of debased and disadvantaged communities. These formative years is where Dr. Ellory was able to cultivate his current philosophy cemented upon one of his favorite quotes by Amos Whitfield. "Nobody cares how much you know till they know how much you care". This philosophy is the foundation upon which "TMC" (Tiny Molar Clinic) is built upon. "Tiny" with "Molar" represents the blending of "Kindness and Care" = Clinic.
</div>
<div class="abs slide kids"><div role="img" aria-label="Group of smiling children leaning in toward the camera" style="background:linear-gradient(135deg,#c9a27c,#7fb0d8)"></div></div>

<h3 class="abs section-title" style="left:165px">About Us</h3>
<h3 class="abs section-title" style="left:416px">Our Gallery</h3>
<h3 class="abs section-title plain" style="left:666px">Appointment</h3>

<div class="abs card" style="left:156px"><div class="photo" role="img" aria-label="Child brushing teeth with a parent" style="background:linear-gradient(135deg,#f1e6dc,#c08a6a)"></div><span class="more">Read more</span></div>
<div class="abs card" style="left:409px"><div class="photo" role="img" aria-label="Circle of smiling children viewed from below" style="background:linear-gradient(135deg,#a8c4e0,#6b4a38)"></div><span class="more">Read more</span></div>
<div class="abs card" style="left:657px"><div class="photo" role="img" aria-label="Smiling senior couple" style="background:linear-gradient(135deg,#d8c0a8,#8a6e58)"></div><span class="more">Read more</span></div>

<div class="abs band"></div>
<div class="abs tagline"><b>beautify</b> your Smiles...</div>

<h4 class="abs sub" style="left:156px">The Services are...</h4>
<ul class="abs services">
  <li>Cleaning/Flouride Treatment</li><li>Preventive Care</li><li>Pedo Partial</li><li>Extractions</li><li>Amalgam Fillings</li><li>Composite Fillings</li><li>Space Maintainers</li><li>Kinder Crowns</li><li>Pulpotomies</li><li>Sealants</li><li>Orthodontics</li><li>Thumb Sucking Appliance</li>
</ul>

<h4 class="abs sub" style="left:408px">Office Map...</h4>
<div class="abs map" role="img" aria-label="Street map showing the office locations"></div>

<h4 class="abs sub" style="left:676px">Contact Us...</h4>
<svg class="abs envelope" width="56" height="44" viewBox="0 0 56 44"><g transform="rotate(-18 28 22)"><rect x="6" y="8" width="44" height="28" fill="#f2f2f2" stroke="#d8d8d8"/><path d="M6 8 L28 24 L50 8" fill="none" stroke="#d8d8d8"/></g></svg>
<div class="abs field" style="top:912px">Name...</div>
<div class="abs field" style="top:942px">Phone...</div>
<div class="abs field" style="top:972px">E-mail...</div>
<div class="abs field" style="top:1003px;height:92px">Message...</div>

<footer class="abs footer">
  <a href="#">About us</a> &nbsp;|&nbsp; <a href="#">Contact Us</a> &nbsp;|&nbsp; <a href="#">Privacy Policy</a> &nbsp;|&nbsp; <a href="#">Terms and Condition</a><br>
  © Copyright &nbsp;Tiny Molar Clinic. All Right Reserved
</footer>

</body>
</html>
```